Business card design Needed for new logo / Construction business, home extensions and new builds

We need a business card design using our new logo files which i will attach to this project :)

We are a small construction business specialising in home extensions, new builds and property development. We are very ambitious and would appreciate professional and elegant designs for our new business card.

Very serious about using the services on MakerQuarry and recently acquired our new logo from here :)

Please get involved, i will feedback when i can as i am very busy but can respond daily, thanks

Target Market(s)

People that want to build onto their houses, new building developments or adding too their existing property

Industry/Entity Type

Construction

Contact Information for Business Card

Renwick Tolliver Construction, Lionel Ashby (Managing Director), Tel 07822254961, email - info@renwick-tolliver, www.renwick-tolliver.co.uk

Colors

Designer to choose colors to be used in the design.

Requirements
Must have
• I like a deep grey on the back please. A lot of you have provided black from and back, try mixing things up a little. The black looks cool 😎 Thanks

```html
<!DOCTYPE html>
<html lang="en">
<head>
<meta charset="utf-8">
<title>Renwick Tolliver Construction – Business Card</title>
<link rel="stylesheet" href="https://fonts.googleapis.com/css2?family=Open+Sans:wght@400;600;700&display=swap">
<style>
  :root {
    --page: #2a2a2c;
    --card-black: #1c1c20;
    --card-grey: #6f7073;
    --grey-ink: #4d4e51;
    --gold-light: #f4c45a;
    --gold: #e0a52e;
    --gold-deep: #b87d17;
    --silver: #d9dadc;
    --white: #f4f4f4;
    --rule: #8a8a8e;
  }
  * { box-sizing: border-box; margin: 0; padding: 0; }
  html, body { width: 1200px; height: 780px; overflow: hidden; }
  body {
    background: var(--page);
    font-family: "Open Sans", Arial, sans-serif;
    position: relative;
  }
  .card {
    position: absolute;
    top: 237px;
    width: 520px;
    height: 306px;
    border-radius: 22px;
    overflow: hidden;
  }
  .card--front { left: 60px; background: var(--card-black); }
  .card--back  { left: 620px; background: var(--card-grey); }

  /* Front: brand block */
  .brand {
    position: absolute;
    left: 34px;
    top: 62px;
    width: 200px;
    display: flex;
    align-items: flex-start;
    gap: 12px;
  }
  .brand__square {
    flex: none;
    width: 22px;
    height: 22px;
    background: var(--gold);
    margin-top: 4px;
  }
  .brand__name {
    color: var(--gold);
    font-weight: 600;
    font-size: 17px;
    line-height: 1.3;
    letter-spacing: 0.06em;
    text-transform: uppercase;
  }
  .divider {
    position: absolute;
    left: 258px;
    top: 36px;
    width: 1px;
    height: 176px;
    background: linear-gradient(to bottom, transparent, var(--rule) 20%, var(--rule) 80%, transparent);
  }

  /* Front: person + contacts */
  .person {
    position: absolute;
    left: 282px;
    top: 50px;
  }
  .person__name {
    font-size: 29px;
    font-weight: 700;
    line-height: 1.1;
    color: var(--white);
  }
  .person__name .surname { color: var(--gold); }
  .person__role {
    font-size: 14px;
    color: var(--white);
    margin-top: 3px;
    letter-spacing: 0.02em;
  }
  .contacts {
    list-style: none;
    margin-top: 16px;
  }
  .contacts li {
    display: flex;
    align-items: center;
    gap: 8px;
    font-size: 13px;
    color: var(--white);
    line-height: 1.75;
  }
  .contacts svg { width: 12px; height: 12px; flex: none; fill: var(--gold); }

  /* Front: address band */
  .band {
    position: absolute;
    left: 0;
    bottom: 26px;
    width: 100%;
    height: 32px;
    background: linear-gradient(to bottom, var(--gold-light), var(--gold) 55%, var(--gold-deep));
    display: flex;
    align-items: center;
    padding-left: 34px;
  }
  .band__address {
    font-size: 13px;
    font-weight: 600;
    color: var(--white);
    letter-spacing: 0.01em;
  }
  .band__end {
    position: absolute;
    right: 0;
    top: 0;
    height: 100%;
    width: 150px;
    background: linear-gradient(to right, var(--gold), var(--silver) 60%);
    display: flex;
    align-items: center;
    justify-content: center;
  }
  .band__mark {
    font-size: 10px;
    font-weight: 600;
    color: var(--card-black);
    letter-spacing: 0.05em;
    text-transform: uppercase;
  }

  /* Back */
  .back-brand {
    position: absolute;
    inset: 0;
    display: flex;
    flex-direction: column;
    align-items: center;
    justify-content: center;
    gap: 14px;
  }
  .back-brand__square {
    width: 34px;
    height: 34px;
    background: var(--grey-ink);
  }
  .back-brand__name {
    color: var(--grey-ink);
    font-weight: 600;
    font-size: 22px;
    letter-spacing: 0.08em;
    text-transform: uppercase;
    text-align: center;
    line-height: 1.35;
  }
</style>
</head>
<body>

<section class="card card--front" aria-label="Business card front">
  <div class="brand">
    <span class="brand__square"></span>
    <p class="brand__name">Renwick Tolliver Construction</p>
  </div>

  <span class="divider"></span>

  <div class="person">
    <h1 class="person__name">Lionel <span class="surname">Ashby</span></h1>
    <p class="person__role">Managing Director</p>
    <ul class="contacts">
      <li>
        <svg viewBox="0 0 24 24" aria-hidden="true"><path d="M6.6 10.8a15.1 15.1 0 0 0 6.6 6.6l2.2-2.2a1 1 0 0 1 1-.25 11.4 11.4 0 0 0 3.6.57 1 1 0 0 1 1 1V20a1 1 0 0 1-1 1A17 17 0 0 1 3 4a1 1 0 0 1 1-1h3.5a1 1 0 0 1 1 1c0 1.25.2 2.45.57 3.57a1 1 0 0 1-.25 1z"/></svg>
        07822 254 961
      </li>
      <li>
        <svg viewBox="0 0 24 24" aria-hidden="true"><path d="M2 5h20v14H2zM4 7v.5l8 5 8-5V7l-8 5z"/></svg>
        info@renwick-tolliver.co.uk
      </li>
      <li>
        <svg viewBox="0 0 24 24" aria-hidden="true"><circle cx="12" cy="12" r="10"/></svg>
        www.renwick-tolliver.co.uk
      </li>
    </ul>
  </div>

  <div class="band">
    <p class="band__address">Quarry Lane, Westbrook Dorset, BH7 2QP</p>
    <div class="band__end"><span class="band__mark">Renwick Tolliver</span></div>
  </div>
</section>

<section class="card card--back" aria-label="Business card back">
  <div class="back-brand">
    <span class="back-brand__square"></span>
    <p class="back-brand__name">Renwick Tolliver<br>Construction</p>
  </div>
</section>

</body>
</html>
```